Email signature and business card

Australian company called Brakmere. We provide construction and maintenance services to the mining industry. I would like the design to be similar to our website theme(www.brakmere.com.au) whilst staying compact. RGB colours to include: 42,96,140 and 232,163,0 and I have attached 2 logos.

The following fields will need to be included:

Full Name
Title
Location/Project
Phone
Mobile
Fax
Email
Web site

Target Market(s)

Mining Industry

Industry/Entity Type

Construction

Requirements
Must have
• Full Name, Title, Office Address, Phone, Mobile, Fax, Email, Web address
• Back of card must include: Boilermaking, Carpentry, Concrete, Construction, Cranes, Data and Comms, Electrical, Fabrication, Fitting, Labour Hire, Plumbing, Rigging, Shutdowns

```html
<!DOCTYPE html>
<html lang="en">
<head>
<meta charset="utf-8">
<title>Brakmere business card</title>
<link rel="stylesheet" href="https://fonts.googleapis.com/css2?family=Open+Sans:wght@400;600;700;800&display=swap">
<style>
  :root {
    --page: #e9e9e7;
    --card-white: #ffffff;
    --card-front: #f3f3f3;
    --brand-blue: #155e78;
    --brand-blue-deep: #0f4c63;
    --brand-yellow: #e8a300;
    --text-light: #ffffff;
    --shadow: rgba(0, 0, 0, 0.22);
  }
  * { margin: 0; padding: 0; box-sizing: border-box; }
  html, body {
    width: 1200px; height: 871px; overflow: hidden;
    background: var(--page);
    font-family: "Open Sans", Arial, sans-serif;
  }
  .canvas { position: relative; width: 1200px; height: 871px; }

  .card {
    position: absolute;
    width: 620px; height: 354px;
    border-radius: 4px;
    box-shadow: 0 10px 28px var(--shadow);
    overflow: hidden;
  }

  /* Logo side */
  .card-front {
    left: 110px; top: 60px;
    background: var(--card-front);
    display: flex; flex-direction: column; align-items: center; justify-content: center;
  }
  .wordmark {
    display: flex; align-items: center; gap: 12px;
  }
  .wordmark-dot {
    width: 34px; height: 34px; border-radius: 50%;
    background: var(--brand-blue);
    flex: none;
  }
  .wordmark-name {
    font-weight: 800; color: var(--brand-blue);
    font-size: 34px; letter-spacing: 0.5px;
    white-space: nowrap;
  }
  .front-url {
    margin-top: 12px;
    font-weight: 700; font-size: 14px; color: var(--brand-blue);
  }
  .services {
    position: absolute; left: 40px; right: 40px; bottom: 30px;
    list-style: none;
    display: flex; flex-wrap: wrap; justify-content: center;
    gap: 4px 0;
    font-size: 11px; font-weight: 600; color: var(--brand-blue);
    letter-spacing: 0.3px;
  }
  .services li { white-space: nowrap; }
  .services li + li::before {
    content: "";
    display: inline-block; width: 4px; height: 4px; border-radius: 50%;
    background: var(--brand-yellow);
    margin: 0 8px; vertical-align: middle;
  }

  /* Contact side */
  .card-back {
    left: 470px; top: 457px;
    background: var(--card-white);
  }
  .card-back .curve { position: absolute; inset: 0; }
  .back-logo {
    position: absolute; left: 0; top: 0; width: 205px; height: 354px;
    display: flex; flex-direction: column; align-items: center; justify-content: center;
  }
  .back-logo .wordmark-dot { width: 20px; height: 20px; }
  .back-logo .wordmark-name { font-size: 21px; }
  .back-logo .wordmark { gap: 8px; }

  .contact {
    position: absolute; left: 290px; top: 62px; right: 20px;
    color: var(--text-light);
  }
  .person-name { font-weight: 700; font-size: 18px; letter-spacing: 0.6px; margin-left: 20px; }
  .person-title { font-size: 12px; margin-left: 20px; margin-top: 1px; }
  .company { font-weight: 700; font-size: 12.5px; margin-top: 24px; }
  .address { font-size: 12.5px; margin-top: 4px; letter-spacing: 0.3px; }
  .lines { list-style: none; margin-top: 14px; }
  .lines li {
    display: flex; align-items: center; gap: 16px;
    font-size: 13px; letter-spacing: 0.6px; height: 24px;
  }
  .lines svg { width: 16px; height: 16px; flex: none; }
  .email { font-size: 13px; letter-spacing: 0.4px; }
</style>
</head>
<body>
<main class="canvas">

  <section class="card card-front" aria-label="Card logo side">
    <div class="wordmark">
      <span class="wordmark-dot"></span>
      <span class="wordmark-name">BRAKMERE</span>
    </div>
    <p class="front-url">www.brakmere.com.au</p>
    <ul class="services" aria-label="Services">
      <li>Boilermaking</li>
      <li>Carpentry</li>
      <li>Concrete</li>
      <li>Construction</li>
      <li>Cranes</li>
      <li>Data and Comms</li>
      <li>Electrical</li>
      <li>Fabrication</li>
      <li>Fitting</li>
      <li>Labour Hire</li>
      <li>Plumbing</li>
      <li>Rigging</li>
      <li>Shutdowns</li>
    </ul>
  </section>

  <section class="card card-back" aria-label="Card contact side">
    <svg class="curve" viewBox="0 0 620 354" width="620" height="354" aria-hidden="true">
      <defs>
        <linearGradient id="panelShade" x1="0" y1="0" x2="1" y2="1">
          <stop offset="0" stop-color="#1a6884"/>
          <stop offset="1" stop-color="#0f4c63"/>
        </linearGradient>
      </defs>
      <path d="M242,0 C212,110 205,250 224,354 L620,354 L620,0 Z" fill="var(--brand-yellow)"/>
      <path d="M252,0 C222,110 215,250 234,354 L620,354 L620,0 Z" fill="url(#panelShade)"/>
    </svg>

    <div class="back-logo">
      <div class="wordmark">
        <span class="wordmark-dot"></span>
        <span class="wordmark-name">BRAKMERE</span>
      </div>
    </div>

    <div class="contact">
      <p class="person-name">Jana Merrick</p>
      <p class="person-title">CEO</p>
      <p class="company">Brakmere, Inc</p>
      <p class="address">Lindenweg 14 CH - 6300 Feldmatt</p>
      <ul class="lines">
        <li>
          <svg viewBox="0 0 16 16" aria-label="Phone"><path d="M3 3h3l1 3-2 1a8 8 0 0 0 4 4l1-2 3 1v3c-6 0-10-4-10-10z" fill="none" stroke="var(--brand-yellow)" stroke-width="1.4" stroke-linejoin="round"/></svg>
          <span>041 555 02 10</span>
        </li>
        <li>
          <svg viewBox="0 0 16 16" aria-label="Mobile"><rect x="4.5" y="1.5" width="7" height="13" rx="1.5" fill="none" stroke="var(--brand-yellow)" stroke-width="1.4"/><circle cx="8" cy="12" r="0.9" fill="var(--brand-yellow)"/></svg>
          <span>041 555 02 10</span>
        </li>
        <li>
          <svg viewBox="0 0 16 16" aria-label="Fax"><rect x="4.5" y="1.5" width="7" height="4" fill="none" stroke="var(--brand-yellow)" stroke-width="1.3"/><rect x="1.5" y="5.5" width="13" height="6" rx="1" fill="none" stroke="var(--brand-yellow)" stroke-width="1.3"/><rect x="4.5" y="9.5" width="7" height="5" fill="none" stroke="var(--brand-yellow)" stroke-width="1.3"/></svg>
          <span>041 555 02 11</span>
        </li>
        <li>
          <svg viewBox="0 0 16 16" aria-label="Email"><rect x="1.5" y="3.5" width="13" height="9" fill="none" stroke="var(--brand-yellow)" stroke-width="1.3"/><path d="M1.5 3.5 8 9l6.5-5.5" fill="none" stroke="var(--brand-yellow)" stroke-width="1.3"/></svg>
          <span class="email">jana@brakmere.com.au</span>
        </li>
      </ul>
    </div>
  </section>

</main>
</body>
</html>
```